Verodex business card

Business card for sustainable investment company called "Verodex". Verodex is an exchange platform selling carbon credits between buyers and sellers. Carbon Credits are an environmental commodity for reducing global carbon emissions.

the card should obviously have our logo and the theme should be sustainability/environment mixed with a trading platform.

Contact Information for Business Card

Logo, Name, Title, Phone, Email

Colors
0054AA
0677BA
7BADD7
CADEEF
E8F1F8
0094D4
00A9DD
6FCCEA
C7EBF8
E9F6FB
00AB8E
00BBA5
67D7C9
C6EFE9
E9F9F6
59FF00
82FF00
B8FF75
E3FFCB
F4FFEA

```html
<!DOCTYPE html>
<html lang="en">
<head>
<meta charset="utf-8">
<title>Verodex Business Card</title>
<link href="https://fonts.googleapis.com/css2?family=Poppins:wght@400;500;600;700&display=swap" rel="stylesheet">
<style>
  :root {
    --backdrop: #b0aaaa;
    --card-navy: #23344f;
    --accent-cyan: #33d9ec;
    --accent-blue: #1f7fe8;
    --rule-blue: #1c6fd6;
    --text-white: #ffffff;
    --text-ink: #0b1320;
  }
  * { margin: 0; padding: 0; box-sizing: border-box; }
  html, body {
    width: 1200px; height: 1015px; overflow: hidden;
    background: var(--backdrop);
    font-family: "Poppins", sans-serif;
  }
  .canvas { position: relative; width: 1200px; height: 1015px; }
  .card {
    position: absolute; left: 195px;
    width: 810px; height: 450px;
    background: var(--card-navy);
    overflow: hidden;
  }
  .card--front { top: 40px; }
  .card--back { top: 525px; }

  .brand { display: flex; align-items: center; gap: 18px; }
  .brand__mark {
    width: 40px; height: 40px;
    background: linear-gradient(135deg, var(--accent-cyan), var(--accent-blue));
  }
  .brand__name {
    color: var(--text-white); font-weight: 600;
    letter-spacing: 2px; text-transform: uppercase;
  }

  .card--front .brand {
    position: absolute; top: 150px; left: 0; right: 0; justify-content: center;
  }
  .card--front .brand__name { font-size: 52px; }

  .web-rule {
    position: absolute; top: 320px; left: 50px; right: 50px;
    display: flex; align-items: center; gap: 16px;
  }
  .web-rule__line { flex: 1; height: 1px; background: var(--rule-blue); }
  .web-rule__text {
    color: var(--accent-cyan); font-size: 19px; letter-spacing: 5px;
  }

  .contact-panel { position: absolute; inset: 0; }
  .contact {
    position: absolute; right: 60px; top: 70px;
    text-align: right; color: var(--text-ink);
  }
  .contact__name { font-size: 30px; font-weight: 700; letter-spacing: 1px; line-height: 1.1; }
  .contact__title { font-size: 20px; font-weight: 500; margin-bottom: 32px; }
  .contact__line {
    display: flex; justify-content: flex-end; align-items: center; gap: 10px;
    font-size: 20px; line-height: 1.45;
  }
  .contact__icon { width: 18px; height: 18px; fill: var(--text-ink); }

  .card--back .brand { position: absolute; left: 50px; bottom: 50px; }
  .card--back .brand__name { font-size: 44px; }
  .card--back .brand__mark { width: 34px; height: 34px; }
</style>
</head>
<body>
<main class="canvas">

  <section class="card card--front">
    <div class="brand">
      <span class="brand__mark"></span>
      <span class="brand__name">Verodex</span>
    </div>
    <div class="web-rule">
      <span class="web-rule__line"></span>
      <span class="web-rule__text">www.verodextrade.com</span>
      <span class="web-rule__line"></span>
    </div>
  </section>

  <section class="card card--back">
    <svg class="contact-panel" viewBox="0 0 810 450" width="810" height="450">
      <defs>
        <linearGradient id="panel-gradient" x1="0" y1="1" x2="1" y2="0">
          <stop offset="0" stop-color="#35e6ec"/>
          <stop offset="1" stop-color="#1f78ea"/>
        </linearGradient>
      </defs>
      <path d="M540 0 L810 0 L810 300 Q810 310 800 316 L660 420 Q645 430 628 423 L462 345 Q448 338 447 322 L438 110 Q438 92 454 82 L540 0 Z"
            fill="url(#panel-gradient)"/>
      <path d="M600 0 L810 0 L810 282 L640 395 L478 318 L470 120 L560 25 Z"
            fill="#ffffff" opacity="0.08"/>
    </svg>

    <div class="contact">
      <p class="contact__name">DANIEL MARSH</p>
      <p class="contact__title">Managing Director</p>
      <p class="contact__line">044-987 210 365
        <svg class="contact__icon" viewBox="0 0 24 24"><path d="M6.6 10.8a15.1 15.1 0 0 0 6.6 6.6l2.2-2.2c.3-.3.7-.4 1-.2 1.1.4 2.3.6 3.6.6.6 0 1 .4 1 1V20c0 .6-.4 1-1 1A17 17 0 0 1 3 4c0-.6.4-1 1-1h3.5c.6 0 1 .4 1 1 0 1.3.2 2.5.6 3.6.1.3 0 .7-.2 1l-2.3 2.2z"/></svg>
      </p>
      <p class="contact__line">hello@verodexmail.com
        <svg class="contact__icon" viewBox="0 0 24 24"><path d="M2 5h20v14H2z M3.5 6.5 12 13l8.5-6.5" fill="var(--text-ink)" stroke="#2aa0e8" stroke-width="1.5"/></svg>
      </p>
      <p class="contact__line">www.verodextrade.com
        <svg class="contact__icon" viewBox="0 0 24 24"><circle cx="12" cy="12" r="10"/><path d="M2 12h20M12 2c3 3 3 17 0 20M12 2c-3 3-3 17 0 20M4 7h16M4 17h16" fill="none" stroke="#2aa0e8" stroke-width="1.2"/></svg>
      </p>
    </div>

    <div class="brand">
      <span class="brand__mark"></span>
      <span class="brand__name">Verodex</span>
    </div>
  </section>

</main>
</body>
</html>
```